Bright and beautiful business card for a coach

I'm a personal and business coach based in Perth, Australia. I need a business card that whilst subtle and elegant, will stand out and appeal on a table full of cards.

My business name is Fern Mentoring and the business card must represent the warmth and brightness implied in the name, without being gimmicky. It must have a warmth and appeal and be easy to read.

I prefer clean, minimalist designs.

It must align with the feel of my website and socials: https://www.fernmentoring-example.com.au/
https://www.instagram.com/fernmentoringau/
https://www.facebook.com/fernmentoringau
Updates

Hi Designers Thank you so much for taking the time to submit designs. I wonder if I could have explained myself a little better. Most of the designs that have been submitted look rather formal and many have quite corporate looking embellishments on them (to my eye). I would like softer, warmer, more organic. I’m open to people playing about and being more abstract, using softer embellishments (e.g the line drawing flowers and grasses I’ve used in my socials) incorporating other colours from my palette or like the social icons in my email signature (in PDF), perhaps playing with size/oversize, playing with the bleed. Please don’t be constrained by what I’ve already done, it merely needs to compliment. I’m sorry if I’m not using the right words or have led you astray. I’m no designer, but I’ve done my website, socials, email signature etc all myself (my logo was a design contest) and I was really hoping for my business card to be something more creative than I could have made with a template. Reminder: No black cards/sides please. Thank you 😊

Target Market(s)

Individuals, most likely but not all female. Creative thinkers. Likely professionals.

Industry/Entity Type

Business & Personal Coach

Contact Information for Business Card

(Fern Mentoring Logo) Name: Greta Pellham; Title: Business & Personal Coach; Phone number: +61 (0)458 913307; Email: greta@fernmentoring-example.com.au; Website: https://fernmentoring-example.com.au; Social icons for Facebook, Instagram & LinkedIn: @fernmentoringAU. Optional strapline: "A thinking partner to help you cut through the noise"

Font styles to use
Sans Serif

Colors
00AB8E
00BBA5
67D7C9
C6EFE9
E9F9F6
59FF00
82FF00
B8FF75
E3FFCB
F4FFEA
FFC000
F8CF3A
FAE287
FDF2CF
FEFAEE

Requirements
Must have
• Must align with feel of my website and socials. Must have a pop of #FFC000 (possibly whole of one side, or at least a block). Bright or white background. Easy to read.
Nice to have
• Possibly incorporate the sunshine/grass picture I have used in website and socials - will upload.
Should not have
• Must not be black or dark. Not impersonal or corporate looking.

```html
<!DOCTYPE html>
<html lang="en">
<head>
<meta charset="utf-8">
<title>Fern Mentoring – Business Card</title>
<link href="https://fonts.googleapis.com/css2?family=Work+Sans:wght@400;500&family=Allura&display=swap" rel="stylesheet">
<style>
  :root {
    --backdrop: #fde7a3;
    --sun-yellow: #fcbf02;
    --amber: #c5771b;
    --slate: #66767a;
    --ink-light: #ffffff;
  }
  * { margin: 0; padding: 0; box-sizing: border-box; }
  html, body {
    width: 1200px;
    height: 800px;
    overflow: hidden;
    background: var(--backdrop);
  }
  .stage {
    position: relative;
    width: 1200px;
    height: 800px;
  }
  .card {
    position: absolute;
    top: 190px;
    width: 240px;
    height: 420px;
    display: block;
  }
  .card--front { left: 345px; }
  .card--back  { left: 620px; }
  .fill-yellow { fill: var(--sun-yellow); }
  .fill-amber  { fill: var(--amber); }
  .fill-slate  { fill: var(--slate); }
  .brand-name {
    font-family: "Work Sans", sans-serif;
    font-weight: 500;
    font-size: 19px;
    letter-spacing: 4px;
    fill: var(--ink-light);
  }
  .person-name {
    font-family: "Allura", cursive;
    font-size: 30px;
    fill: var(--ink-light);
  }
  .contact {
    font-family: "Work Sans", sans-serif;
    font-weight: 400;
    fill: var(--ink-light);
  }
  .contact--title { font-size: 8.6px; letter-spacing: 0.3px; }
  .contact--line  { font-size: 7.6px; }
  .divider { stroke: var(--ink-light); stroke-width: 0.8; }
  .handle-dot { fill: var(--ink-light); }
</style>
</head>
<body>
<main class="stage">

  <!-- Front of card -->
  <svg class="card card--front" viewBox="0 0 240 420" aria-label="Card front: Fern Mentoring">
    <defs>
      <clipPath id="front-clip"><rect width="240" height="420"/></clipPath>
    </defs>
    <g clip-path="url(#front-clip)">
      <rect class="fill-amber" width="240" height="420"/>
      <circle class="fill-slate" cx="250" cy="-60" r="128"/>
      <path class="fill-yellow" d="M0,97 C140,110 262,240 233,420 L0,420 Z"/>
      <text class="brand-name" transform="translate(130,380) rotate(-90)">FERN MENTORING</text>
    </g>
  </svg>

  <!-- Back of card -->
  <svg class="card card--back" viewBox="0 0 240 420" aria-label="Card back: contact details for Greta Pellham">
    <defs>
      <clipPath id="back-clip"><rect width="240" height="420"/></clipPath>
    </defs>
    <g clip-path="url(#back-clip)">
      <rect class="fill-yellow" width="240" height="420"/>
      <circle class="fill-slate" cx="23" cy="138" r="54"/>
      <circle class="fill-slate" cx="250" cy="300" r="60"/>
      <path class="fill-amber" d="M85,114 H240 V305 H85 A95.5,95.5 0 0 1 85,114 Z"/>

      <g class="contact-block">
        <text class="person-name" transform="translate(82,283) rotate(-90)">Greta Pellham</text>
        <text class="contact contact--title" transform="translate(98,277) rotate(-90)">Business &amp; Personal Coach</text>
        <line class="divider" x1="111" y1="283" x2="111" y2="135"/>
        <text class="contact contact--line" transform="translate(134,278) rotate(-90)">greta@fernmentoring-example.com.au</text>
        <text class="contact contact--line" transform="translate(151,253) rotate(-90)">+61 (0)458 913307</text>
        <text class="contact contact--line" transform="translate(167,272) rotate(-90)">https://fernmentoring-example.com.au</text>
        <circle class="handle-dot" cx="187" cy="246" r="4"/>
        <text class="contact contact--line" transform="translate(190,238) rotate(-90)">@fernmentoringAU</text>
      </g>
    </g>
  </svg>

</main>
</body>
</html>
```